Vernac Law Business cards and stationary design project

We are looking for a stationary design for business cards (double sided), 8x10, 5x7, and legal and standard envelopes.

We would like the design to match the logo that we have already.
Color palate preferred is Teal, White, grey and any others that will look good for a professional law firm.

We would like this statement: "RELATIONSHIPS. RESPECT. RESULT" to be on the back of the business cards and maybe on the stationary if it looks good.

Please see link to website for more information: www.vernac-law.example

Target Market(s)

Potential clients that need Attorney services.

Industry/Entity Type

Law Firm

Contact Information for Business Card

We would like the front and back to be two different colors. Current business cards are teal front, grey back and are a vertical design. We are open to options with colors.

Font styles to use
Serif

Colors
33a6d7
33b8a4
b9b9b9
5c5c5c

Requirements
Must have
• Logo supplied needs to go on the card and stationary.
• Match website color palate, www.vernac-law.example
• Be professional and not too wordy.
• Criminal Law, Civil Litigation, Personal Injury, Restraining Orders need to be on the card.
Nice to have
• RELATIONSHIPS. RESPECT. RESULTS. on the back of the card.
Should not have
• Not be too busy/wordy or too flashy.

```html
<!DOCTYPE html>
<html lang="en">
<head>
<meta charset="utf-8">
<title>Vernac Law – Business Card</title>
<link rel="stylesheet" href="https://fonts.googleapis.com/css2?family=Open+Sans:wght@400;600;700&display=swap">
<style>
  :root {
    --teal: #138896;
    --teal-text: #1a8a97;
    --teal-faint: #cfe6ea;
    --ink: #1c1c1c;
    --paper: #ffffff;
    --backdrop: #2f3136;
  }
  * { box-sizing: border-box; margin: 0; padding: 0; }
  html, body {
    width: 1200px; height: 864px; overflow: hidden;
    background: var(--backdrop);
    font-family: "Open Sans", Arial, sans-serif;
  }
  .canvas { position: relative; width: 1200px; height: 864px; }
  .card {
    position: absolute; width: 580px; height: 330px;
    background: var(--paper); overflow: hidden;
    box-shadow: 0 10px 26px rgba(0,0,0,.45);
  }
  .card--front { left: 170px; top: 80px; }
  .card--back { left: 450px; top: 450px; }

  /* front */
  .brand {
    position: absolute; left: 0; right: 0; top: 100px;
    display: flex; align-items: center; justify-content: center; gap: 14px;
  }
  .brand__mark { width: 22px; height: 22px; border-radius: 50%; background: var(--teal); }
  .brand__name {
    color: var(--teal-text); font-weight: 600; font-size: 40px;
    letter-spacing: 4px; text-transform: uppercase;
  }
  .tagline {
    position: absolute; left: 0; right: 0; top: 222px; text-align: center;
    color: var(--teal-text); font-weight: 600; font-size: 15px; letter-spacing: .3px;
  }

  /* back */
  .back__decor {
    position: absolute; right: 30px; top: 10px; width: 240px; height: 240px;
    border-radius: 50%; background: var(--teal-faint);
  }
  .contact { position: absolute; left: 34px; top: 26px; color: var(--ink); }
  .contact__name { color: var(--teal-text); font-weight: 700; font-size: 21px; line-height: 1.1; }
  .contact__title { font-size: 13.5px; margin-bottom: 14px; }
  .contact__address { font-size: 14px; line-height: 1.2; margin-bottom: 10px; }
  .contact__list { list-style: none; font-size: 14px; }
  .contact__list li { display: flex; align-items: center; gap: 10px; height: 21px; }
  .contact__list svg { width: 12px; height: 12px; fill: var(--teal); flex: none; }
  .practice-band {
    position: absolute; left: 0; right: 0; bottom: 0; height: 92px;
    background: var(--teal); color: var(--paper);
    display: flex; align-items: center; justify-content: center; text-align: center;
    font-weight: 600; font-size: 15px; line-height: 1.35; padding: 0 30px;
  }
</style>
</head>
<body>
<main class="canvas">
  <section class="card card--front" aria-label="Card front">
    <div class="brand">
      <span class="brand__mark"></span>
      <span class="brand__name">Vernac Law</span>
    </div>
    <p class="tagline">Realtionships | Respect | Result</p>
  </section>

  <section class="card card--back" aria-label="Card back">
    <div class="back__decor"></div>
    <div class="contact">
      <h1 class="contact__name">Daniel Mercer</h1>
      <p class="contact__title">Managing Director</p>
      <p class="contact__address">12345, Address Goes Here<br>Country Name, 123456</p>
      <ul class="contact__list">
        <li><svg viewBox="0 0 24 24"><path d="M6.6 10.8a15.1 15.1 0 0 0 6.6 6.6l2.2-2.2c.3-.3.7-.4 1-.2 1.1.4 2.3.6 3.6.6.6 0 1 .4 1 1V20c0 .6-.4 1-1 1A17 17 0 0 1 3 4c0-.6.4-1 1-1h3.5c.6 0 1 .4 1 1 0 1.3.2 2.5.6 3.6.1.3 0 .7-.2 1z"/></svg>(044)-456-7890</li>
        <li><svg viewBox="0 0 24 24"><path d="M6 2h9v6H6zM3 9h18v11H3zm4 3v2h3v-2zm0 4v2h3v-2zm6-4v2h4v-2zm0 4v2h4v-2z"/></svg>123-456-7890</li>
        <li><svg viewBox="0 0 24 24"><path d="M2 5h20v14H2zm2 2v.5l8 5 8-5V7l-8 5z"/></svg>info@youremail.com</li>
        <li><svg viewBox="0 0 24 24"><circle cx="12" cy="12" r="10"/></svg>www.website.com</li>
      </ul>
    </div>
    <div class="practice-band">Practice areas, Criminal Law, Civil Litigation/Personal Injury<br>Restraining Orders</div>
  </section>
</main>
</body>
</html>
```